Specialised investor in e-mobility and energy wants business card design

We need a business card design that fits our existing corporate design. <The look and feel must be 'sharp'/'clean', dynamic, communicate momentum, professionalism etc (as one would imagine from a firm in the financial sector). We like the idea of a reverse-side of the card that includes the logo, and the name and contact details on the other. We expect the deliverable to be whatever format might be required to be able to get cards printed directly by a service such as kelmo press. Our website is www.zub.capital

```html
<!DOCTYPE html>
<html lang="en">
<head>
<meta charset="utf-8">
<title>Zub Capital – Business Card</title>
<link href="https://fonts.googleapis.com/css2?family=Questrial&family=Lato:wght@400;700&display=swap" rel="stylesheet">
<style>
  :root {
    --bg: #e4e5e6;
    --card: #ffffff;
    --card-shade: #f1f1f1;
    --green-dark: #1f4d1a;
    --green: #6aa336;
    --ink: #3a3a3a;
    --line: #7cb342;
  }
  * { box-sizing: border-box; margin: 0; padding: 0; }
  html, body { width: 1200px; height: 900px; overflow: hidden; }
  body {
    background: var(--bg);
    display: flex;
    flex-direction: column;
    align-items: center;
    justify-content: center;
    gap: 60px;
    font-family: "Lato", sans-serif;
  }
  .card {
    position: relative;
    width: 630px;
    height: 360px;
    border-radius: 34px;
    background: linear-gradient(120deg, var(--card-shade) 0%, var(--card) 55%, var(--card-shade) 100%);
    box-shadow: 0 6px 18px rgba(0,0,0,0.18);
    overflow: hidden;
  }
  .wordmark {
    display: flex;
    align-items: center;
    gap: 12px;
    font-family: "Questrial", sans-serif;
    color: var(--green-dark);
    font-size: 58px;
    line-height: 1;
  }
  .wordmark-dot {
    width: 16px; height: 16px;
    border-radius: 50%;
    background: var(--green);
  }
  /* front */
  .card-front .brand {
    position: absolute;
    left: 0; right: 0; top: 110px;
    display: flex; justify-content: center;
  }
  .card-front .rule {
    position: absolute;
    left: 95px; right: 95px; top: 196px;
    height: 2px;
    background: var(--line);
  }
  .card-front .site {
    position: absolute;
    left: 0; right: 0; top: 214px;
    text-align: center;
    font-family: "Questrial", sans-serif;
    font-size: 15px;
    letter-spacing: 6px;
    color: var(--ink);
  }
  /* back */
  .card-back .brand {
    position: absolute;
    right: 52px; top: 42px;
  }
  .card-back .brand .wordmark { font-size: 50px; }
  .contact {
    position: absolute;
    left: 48px; bottom: 40px;
    display: flex;
    align-items: stretch;
    gap: 26px;
  }
  .person-name {
    color: var(--green);
    font-weight: 700;
    font-size: 21px;
    letter-spacing: 0.5px;
    text-transform: uppercase;
  }
  .person-role {
    color: var(--ink);
    font-size: 16px;
    margin: 2px 0 14px 16px;
  }
  .contact-list { list-style: none; margin-left: 40px; }
  .contact-list li {
    display: flex; align-items: center; gap: 10px;
    font-size: 16px; color: var(--ink);
    line-height: 26px;
  }
  .contact-list svg { width: 16px; height: 16px; flex: none; }
  .divider { width: 1.5px; background: var(--green-dark); margin-top: 40px; }
  .company { padding-top: 40px; }
  .company-name { color: var(--green); font-weight: 700; font-size: 18px; }
  .company-city { color: var(--ink); font-size: 16px; margin-left: 18px; }
</style>
</head>
<body>

<section class="card card-front" aria-label="Card front">
  <div class="brand">
    <div class="wordmark"><span class="wordmark-dot"></span>Zub Capital</div>
  </div>
  <div class="rule"></div>
  <p class="site">www.zub.capital</p>
</section>

<section class="card card-back" aria-label="Card back">
  <div class="brand">
    <div class="wordmark"><span class="wordmark-dot"></span>Zub Capital</div>
  </div>

  <div class="contact">
    <div class="person">
      <p class="person-name">Marc Hollis</p>
      <p class="person-role">Partner</p>
      <ul class="contact-list">
        <li>
          <svg viewBox="0 0 16 16" aria-hidden="true"><rect x="4" y="1" width="8" height="14" rx="1.5" fill="none" stroke="#6aa336" stroke-width="1.4"/><line x1="7" y1="12.5" x2="9" y2="12.5" stroke="#6aa336" stroke-width="1.4"/></svg>
          +41 79000 1234
        </li>
        <li>
          <svg viewBox="0 0 16 16" aria-hidden="true"><rect x="1" y="3.5" width="14" height="9.5" rx="1" fill="#6aa336"/><path d="M1.5 4l6.5 5 6.5-5" fill="none" stroke="#fff" stroke-width="1.2"/></svg>
          marc@zub.capital
        </li>
        <li>
          <svg viewBox="0 0 16 16" aria-hidden="true"><circle cx="7" cy="7" r="5.5" fill="none" stroke="#6aa336" stroke-width="1.4"/><path d="M1.5 7h11M7 1.5c-2.5 3-2.5 8 0 11M7 1.5c2.5 3 2.5 8 0 11" fill="none" stroke="#6aa336" stroke-width="1"/><line x1="11" y1="11" x2="15" y2="15" stroke="#6aa336" stroke-width="1.6"/></svg>
          www.zub.capital
        </li>
      </ul>
    </div>
    <div class="divider"></div>
    <div class="company">
      <p class="company-name">Zub Capital S.A.</p>
      <p class="company-city">Geneva, Switzerland</p>
    </div>
  </div>
</section>

</body>
</html>
```